Brell Stone Company Business Cards

Front and Back Business Card - logo and text setup - cool design. I need workable photoshop or illustrator files so I can setup each employee card with design that is created
Updates

Hi everyone, thank you for the great entries. Please no more white and blue cards - there are so many already - black and silver only now please. thanks!

Target Market(s)

Construction Industry - Facility Managers

Industry/Entity Type

Construction

Contact Information for Business Card

I really like contemporary simplistic looks - clean neat....not opposed to seeing some black backrounds

Requirements
Must have
• Logo/website address with design on front only - www.brellstone-example.com (logo attached)
• Back:
• Name/Title/Company Address/Phone/email address
Nice to have
• Cool design
Should not have
• Nothing gimmicky like Fire or Water - since we are a Fire Protection company - it has all been done

```html
<!DOCTYPE html>
<html lang="en">
<head>
<meta charset="utf-8">
<title>Brell Stone Company Business Cards</title>
<link href="https://fonts.googleapis.com/css2?family=Lato:wght@700;900&family=Roboto:wght@300&display=swap" rel="stylesheet">
<style>
  :root {
    --page: #dcdcdc;
    --card-black: #1b1c1e;
    --card-black-deep: #141517;
    --silver-bright: #e4e4e4;
    --silver: #c4c6c9;
    --silver-mid: #9a9da2;
    --silver-dark: #7c7f84;
  }
  * { margin: 0; padding: 0; box-sizing: border-box; }
  html, body { width: 1125px; height: 1200px; overflow: hidden; }
  body { background: var(--page); position: relative; }

  .card {
    position: absolute;
    left: 156px;
    width: 826px;
    height: 472px;
    overflow: hidden;
    background: var(--card-black);
  }
  .card--front { top: 106px; background: var(--card-black-deep); }
  .card--back  { top: 639px; }

  .card__band {
    position: absolute; left: 0; bottom: 0;
    width: 100%; height: 13px;
    background: linear-gradient(90deg, var(--silver-dark), var(--silver-bright) 50%, var(--silver-dark));
  }

  .wordmark {
    position: absolute;
    display: flex; align-items: center; gap: 12px;
    font-family: "Lato", sans-serif;
    font-weight: 900;
    white-space: nowrap;
    color: var(--silver);
  }
  .wordmark__square { display: block; background: var(--silver); }
  .card--front .wordmark { left: 116px; top: 196px; font-size: 48px; }
  .card--front .wordmark__square { width: 16px; height: 16px; }
  .card--back .wordmark {
    left: 0; right: 0; top: 190px; justify-content: center;
    font-size: 78px;
  }
  .card--back .wordmark__square { width: 24px; height: 24px; }

  .contact {
    position: absolute; left: 489px; top: 96px;
    font-family: "Roboto", sans-serif; font-weight: 300;
    color: var(--silver-mid); font-size: 19.5px; line-height: 25px;
  }
  .contact__name {
    font-family: "Lato", sans-serif; font-weight: 700;
    color: var(--silver-bright); font-size: 30px; line-height: 34px;
  }
  .contact__title {
    font-family: "Lato", sans-serif; font-weight: 700;
    color: var(--silver); font-size: 20px; line-height: 24px;
    margin-bottom: 22px;
  }
  .contact__address { margin-bottom: 10px; }
  .contact__lines { margin-bottom: 20px; }
  .contact__web { letter-spacing: 2.4px; font-size: 18px; }
</style>
</head>
<body>
  <section class="card card--front" aria-label="Business card front">
    <div class="wordmark"><span class="wordmark__square"></span>Brell Stone</div>
    <div class="contact">
      <p class="contact__name">Daniel Marsh</p>
      <p class="contact__title">CEO/Founder</p>
      <p class="contact__address">48 Harbor Point Road<br>Millbrook, NY 12545</p>
      <p class="contact__lines">Tel: (555) 014-2270<br>Fax: (555) 014-2271<br>info@brellstone-example.com</p>
      <p class="contact__web">www.brellstone-example.com</p>
    </div>
    <div class="card__band"></div>
  </section>

  <section class="card card--back" aria-label="Business card back">
    <div class="wordmark"><span class="wordmark__square"></span>Brell Stone</div>
    <div class="card__band"></div>
  </section>
</body>
</html>
```